Print and E-book Personal Injury Front and Back Book Cover

I need a book cover for a personal injury law firm book titled "Steady Ground Ahead" with the subtitle "A Practical Guide for Accident Claims." The book cover should have an image. This isas a lead generation book designed to be give to potential clients to have them sign as new clients.

Target Market(s)

Potential New Clients Looking For a Personal Injury Attorney

Industry/Entity Type

Legal

Requirements
Must have
• Title and some type of image or images

```html
<!DOCTYPE html>
<html lang="en">
<head>
<meta charset="utf-8">
<title>Steady Ground Ahead – Book Cover Wrap</title>
<link rel="stylesheet" href="https://fonts.googleapis.com/css2?family=Cinzel:wght@500;700&family=Oswald:wght@600&family=Open+Sans:wght@400&display=swap">
<style>
  :root {
    --page-bg: #ffffff;
    --ink-black: #050607;
    --photo-deep: #0d1626;
    --photo-mid: #3a5076;
    --photo-light: #a9bcdb;
    --photo-pale: #dbe4f2;
    --gold: #c9a640;
    --gold-light: #ecd689;
    --gold-dark: #9c7a22;
    --blurb: #c9d1dc;
  }
  * { margin: 0; padding: 0; box-sizing: border-box; }
  html, body {
    width: 1200px; height: 288px; overflow: hidden;
    background: var(--page-bg);
  }
  .canvas {
    width: 1200px; height: 288px;
    display: flex; align-items: center; justify-content: center;
  }
  .cover-wrap {
    position: relative;
    width: 420px; height: 288px;
    display: flex;
    background: var(--ink-black);
  }
  .gold-text {
    color: var(--gold);
    background: linear-gradient(180deg, var(--gold-light) 0%, var(--gold) 55%, var(--gold-dark) 100%);
    -webkit-background-clip: text; background-clip: text;
    -webkit-text-fill-color: transparent;
  }

  /* Back cover */
  .back-cover {
    position: relative; width: 192px; height: 100%; overflow: hidden;
  }
  .back-photo {
    position: absolute; inset: 0;
    background:
      radial-gradient(ellipse 60% 45% at 30% 22%, rgba(120,140,170,0.35) 0%, rgba(40,52,70,0.25) 50%, rgba(0,0,0,0) 100%),
      radial-gradient(ellipse 70% 60% at 75% 60%, rgba(60,72,92,0.35) 0%, rgba(0,0,0,0) 100%),
      linear-gradient(180deg, #141b26 0%, #0a0e15 55%, #050608 100%);
  }
  .back-content {
    position: relative; padding: 28px 18px 0; text-align: center;
  }
  .back-title {
    font-family: "Cinzel", serif; font-weight: 500;
    font-size: 19px; line-height: 16px;
  }
  .back-title .title-accent {
    display: block; font-family: "Oswald", sans-serif; font-weight: 600;
    font-size: 22px; line-height: 24px;
  }
  .back-subtitle {
    font-family: "Cinzel", serif; font-weight: 700;
    font-size: 8.4px; line-height: 8.6px; margin-top: 1px;
  }
  .blurb {
    font-family: "Open Sans", sans-serif; font-size: 5.2px; line-height: 10.7px;
    color: var(--blurb); text-align: justify; text-align-last: center;
    margin-top: 3px;
  }
  .blurb + .blurb { margin-top: 10px; }

  /* Spine */
  .spine {
    width: 36px; height: 100%; background: var(--ink-black);
    display: flex; flex-direction: column; align-items: center;
    padding: 16px 0 0;
  }
  .spine-title, .spine-author {
    writing-mode: vertical-rl; white-space: nowrap;
  }
  .spine-title {
    font-family: "Cinzel", serif; font-weight: 500; font-size: 14px; letter-spacing: 0.4px;
    height: 182px;
  }
  .spine-title .title-accent {
    font-family: "Oswald", sans-serif; font-weight: 600; font-size: 15px;
  }
  .spine-author {
    margin-top: 12px;
    font-family: "Cinzel", serif; font-weight: 500; font-size: 9px; letter-spacing: 0.4px;
  }

  /* Front cover */
  .front-cover {
    position: relative; width: 192px; height: 100%; overflow: hidden;
  }
  .front-photo {
    position: absolute; inset: 0;
    background:
      radial-gradient(ellipse 55% 40% at 78% 28%, var(--photo-pale) 0%, rgba(169,188,219,0.55) 40%, rgba(0,0,0,0) 100%),
      radial-gradient(ellipse 45% 60% at 38% 45%, rgba(150,170,205,0.55) 0%, rgba(0,0,0,0) 100%),
      linear-gradient(90deg, rgba(6,10,18,0.75) 0%, rgba(6,10,18,0) 30%),
      linear-gradient(180deg, var(--photo-mid) 0%, #253655 50%, var(--photo-deep) 80%, #04060b 100%);
  }
  .front-content {
    position: relative; height: 100%; text-align: center;
  }
  .front-subtitle {
    position: absolute; top: 17px; left: 0; right: 0;
    font-family: "Cinzel", serif; font-weight: 700;
    font-size: 11px; line-height: 11px;
  }
  .front-title {
    position: absolute; top: 128px; left: 0; right: 0;
    font-family: "Cinzel", serif; font-weight: 500;
    font-size: 34px; line-height: 33px;
  }
  .front-title .title-accent {
    display: block; font-family: "Oswald", sans-serif; font-weight: 600;
    font-size: 46px; line-height: 44px;
  }
  .front-author {
    position: absolute; top: 255px; left: 0; right: 0;
    font-family: "Cinzel", serif; font-weight: 500; font-size: 13px; letter-spacing: 0.4px;
  }
</style>
</head>
<body>
<main class="canvas">
  <article class="cover-wrap">
    <section class="back-cover">
      <div class="back-photo" role="img" aria-label="Photo area: darkened, faded view of a Lady Justice statue holding scales beside window blinds"></div>
      <div class="back-content">
        <h2 class="back-title gold-text">STEADY<br>GROUND<span class="title-accent">AHEAD</span></h2>
        <p class="back-subtitle gold-text">A PRACTICAL GUIDE<br>FOR ACCIDENT CLAIMS</p>
        <p class="blurb">After an accident, questions pile up faster than bills. This guide explains your rights in plain language, walks through each stage of a claim, and shows what insurers look for. Learn how fault is decided, why records matter, and which early steps protect the value of your case.</p>
        <p class="blurb">Inside you will find checklists for medical care, tips on talking with adjusters, and a clear timeline from first call to settlement. Written for injured people and their families, it offers steady support so you can focus on healing while your claim moves forward.</p>
      </div>
    </section>
    <section class="spine">
      <h2 class="spine-title gold-text">STEADY GROUND <span class="title-accent">AHEAD</span></h2>
      <p class="spine-author gold-text">AUTHOR NAME</p>
    </section>
    <section class="front-cover">
      <div class="front-photo" role="img" aria-label="Photo area: blue-toned Lady Justice statue raising her scales in front of sunlit window blinds and law books"></div>
      <div class="front-content">
        <p class="front-subtitle gold-text">A PRACTICAL GUIDE<br>FOR ACCIDENT CLAIMS</p>
        <h1 class="front-title gold-text">STEADY<br>GROUND<span class="title-accent">AHEAD</span></h1>
        <p class="front-author gold-text">AUTHOR NAME</p>
      </div>
    </section>
  </article>
</main>
</body>
</html>
```